Poetry Book Cover Design Project

Looking for a minimalistic book cover design for a collection of poems. The book title is "Before The Lanterns Drift Away Slowly". There are three parts to the book. First covers poetry in the theme of Rage. Second love and desire. The third is strange poems. Essentially the sections are "Rage", "Desire" and the "Strange". The reason for the title "Before The Lanterns Drift Away Slowly" is as if someone is writing these till life changes towards the intended outcome as felt in each poem. I want to have the author's name "Ruvinath Kolongaswe" at the bottom. Ilustration attached.
- Minimalistic

```html
<!DOCTYPE html>
<html lang="en">
<head>
<meta charset="UTF-8">
<title>Before The Lanterns Drift Away Slowly — Cover</title>
<link rel="stylesheet" href="https://fonts.googleapis.com/css2?family=Federo&family=Josefin+Sans:wght@600&display=swap">
<style>
  :root {
    --stage: #d9d1ca;
    --paper: #fbfbfa;
    --ink: #0d0d0d;
    --band-text: #f4f4f4;
  }
  html, body {
    margin: 0;
    padding: 0;
    width: 1200px;
    height: 800px;
    overflow: hidden;
    background: var(--stage);
  }
  .canvas {
    position: relative;
    width: 1200px;
    height: 800px;
    display: flex;
    align-items: center;
    justify-content: center;
  }
  .cover {
    position: relative;
    width: 440px;
    height: 660px;
    background: var(--paper);
    box-shadow: 0 10px 30px rgba(60, 45, 35, 0.18);
  }
  .title {
    position: absolute;
    top: 60px;
    left: 60px;
    right: 40px;
    margin: 0;
    font-family: "Federo", sans-serif;
    font-weight: 400;
    color: var(--ink);
    text-transform: uppercase;
    line-height: 0.92;
    display: flex;
    flex-direction: column;
    align-items: flex-end;
  }
  .title span { display: block; letter-spacing: -1px; }
  .title .w1 { font-size: 74px; margin-right: 30px; }
  .title .w2 { font-size: 62px; margin-right: 70px; }
  .title .w3 { font-size: 52px; margin-right: 0; }
  .title .w4 { font-size: 46px; margin-right: 90px; }
  .title .w5 { font-size: 66px; margin-right: 14px; }
  .title .w6 { font-size: 66px; margin-right: 36px; }
  .figure {
    position: absolute;
    left: 88px;
    top: 518px;
    width: 18px;
    height: 64px;
    background: var(--ink);
    border-radius: 6px 6px 2px 2px;
  }
  .author-band {
    position: absolute;
    left: 80px;
    right: 0;
    top: 584px;
    height: 36px;
    background: var(--ink);
    display: flex;
    align-items: center;
    padding-left: 14px;
  }
  .author {
    margin: 0;
    font-family: "Josefin Sans", sans-serif;
    font-weight: 600;
    font-size: 15px;
    letter-spacing: 3.5px;
    color: var(--band-text);
    text-transform: uppercase;
    padding-top: 3px;
  }
</style>
</head>
<body>
  <main class="canvas">
    <section class="cover">
      <h1 class="title">
        <span class="w1">Before</span>
        <span class="w2">The</span>
        <span class="w3">Lanterns</span>
        <span class="w4">Drift</span>
        <span class="w5">Away</span>
        <span class="w6">Slowly</span>
      </h1>
      <div class="figure" role="img" aria-label="Small silhouette of a standing man"></div>
      <div class="author-band">
        <p class="author">Ruvinath&nbsp;&nbsp;Kolongaswe</p>
      </div>
    </section>
  </main>
</body>
</html>
```